Business card design Needed for new logo / Construction business, home extensions and new builds

We need a business card design using our new logo files which i will attach to this project :)

We are a small construction business specialising in home extensions, new builds and property development. We are very ambitious and would appreciate professional and elegant designs for our new business card.

Very serious about using the services on MakerQuarry and recently acquired our new logo from here :)

Please get involved, i will feedback when i can as i am very busy but can respond daily, thanks

Target Market(s)

People that want to build onto their houses, new building developments or adding too their existing property

Industry/Entity Type

Construction

Contact Information for Business Card

Renwick Tolliver Construction, Lionel Ashby (Managing Director), Tel 07822254961, email - info@renwick-tolliver, www.renwick-tolliver.co.uk

Colors

Designer to choose colors to be used in the design.

Requirements
Must have
• I like a deep grey on the back please. A lot of you have provided black from and back, try mixing things up a little. The black looks cool 😎 Thanks

```html
<!DOCTYPE html>
<html lang="en">
<head>
<meta charset="utf-8">
<title>Renwick Tolliver Construction – Business Card</title>
<link href="https://fonts.googleapis.com/css2?family=Lato:wght@400;700;900&display=swap" rel="stylesheet">
<style>
  :root {
    --page-bg: #e4e4e4;
    --card-black: #1c1c1c;
    --card-grey: #242424;
    --gold: #d9a21e;
    --gold-light: #f6c84a;
    --gold-dark: #b07a10;
    --silver: #c9c9c9;
    --text-light: #e6e6e6;
    --text-muted: #b8b8b8;
    --emboss: #5a5a5a;
    --url-ink: #2a1d04;
  }
  * { box-sizing: border-box; margin: 0; padding: 0; }
  html, body { width: 1200px; height: 982px; overflow: hidden; }
  body {
    background: var(--page-bg);
    font-family: "Lato", Arial, sans-serif;
    position: relative;
  }
  .card {
    position: absolute;
    left: 290px;
    width: 620px;
    height: 354px;
    border-radius: 22px;
    overflow: hidden;
    box-shadow: 0 10px 24px rgba(0,0,0,0.18);
  }
  .card--back { top: 110px; background: var(--card-grey); }
  .card--front { top: 518px; background: var(--card-black); }

  .wordmark {
    font-weight: 700;
    text-transform: uppercase;
    text-align: center;
    letter-spacing: 2px;
    line-height: 1.15;
  }
  .card--back .wordmark {
    position: absolute;
    left: 0; right: 0; top: 112px;
    font-size: 36px;
    color: var(--emboss);
  }
  .card--back .wordmark-mark {
    display: block;
    width: 24px; height: 24px;
    margin: 0 auto 16px;
    background: var(--emboss);
  }

  .brand-block {
    position: absolute;
    left: 18px; top: 82px;
    width: 294px;
  }
  .brand-block .wordmark {
    font-size: 26px;
    color: var(--gold);
  }
  .brand-block .wordmark-mark {
    display: block;
    width: 22px; height: 22px;
    margin: 0 auto 14px;
    background: var(--gold);
  }

  .divider {
    position: absolute;
    left: 330px; top: 48px;
    width: 2px; height: 232px;
    background: var(--gold);
  }

  .contact {
    position: absolute;
    left: 356px; top: 46px;
    width: 250px;
  }
  .contact-name {
    font-weight: 900;
    font-size: 30px;
    color: var(--gold);
    text-transform: uppercase;
    letter-spacing: 0.5px;
    line-height: 1.05;
  }
  .contact-role {
    font-size: 17px;
    color: var(--text-muted);
    margin: 4px 0 14px;
  }
  .contact-list { list-style: none; }
  .contact-list li {
    display: flex;
    align-items: flex-start;
    gap: 10px;
    font-size: 15px;
    color: var(--text-light);
    line-height: 1.3;
    margin-bottom: 5px;
  }
  .contact-list svg { flex: none; width: 14px; height: 14px; margin-top: 2px; fill: var(--gold); }

  .footer-band {
    position: absolute;
    left: 0; right: 0; bottom: 0;
    height: 58px;
    background: linear-gradient(90deg, var(--gold-light) 0%, var(--gold-dark) 30%, var(--gold-light) 65%, var(--gold-dark) 100%);
    border-top: 5px solid var(--silver);
    display: flex;
    align-items: center;
    justify-content: center;
  }
  .footer-url {
    font-size: 16px;
    letter-spacing: 3px;
    text-transform: uppercase;
    color: var(--url-ink);
  }
</style>
</head>
<body>

  <section class="card card--back" aria-label="Card back">
    <div class="wordmark">
      <span class="wordmark-mark"></span>
      Renwick Tolliver<br>Construction
    </div>
  </section>

  <section class="card card--front" aria-label="Card front">
    <div class="brand-block">
      <div class="wordmark">
        <span class="wordmark-mark"></span>
        Renwick Tolliver<br>Construction
      </div>
    </div>

    <div class="divider"></div>

    <div class="contact">
      <h1 class="contact-name">Lionel Ashby</h1>
      <p class="contact-role">Managing Director</p>
      <ul class="contact-list">
        <li>
          <svg viewBox="0 0 14 14"><path d="M7 0a5 5 0 0 0-5 5c0 3.5 5 9 5 9s5-5.5 5-9a5 5 0 0 0-5-5zm0 7a2 2 0 1 1 0-4 2 2 0 0 1 0 4z"/></svg>
          <span>Your Address, City<br>State, Zip 1235</span>
        </li>
        <li>
          <svg viewBox="0 0 14 14"><path d="M3 1l2.5 3-1.5 1.5c.8 1.8 2.2 3.2 4 4L9.5 8l3 2.5-1.5 2.5C6 13 1 8 1 2.5z"/></svg>
          <span>07822254961</span>
        </li>
        <li>
          <svg viewBox="0 0 14 14"><path d="M4 0h6a1 1 0 0 1 1 1v12a1 1 0 0 1-1 1H4a1 1 0 0 1-1-1V1a1 1 0 0 1 1-1zm0 2v9h6V2zm3 9.5a.8.8 0 1 0 0 1.6.8.8 0 0 0 0-1.6z"/></svg>
          <span>07822254978</span>
        </li>
        <li>
          <svg viewBox="0 0 14 14"><path d="M3 0h8v4H3zM1 5h12a1 1 0 0 1 1 1v5h-3v3H3v-3H0V6a1 1 0 0 1 1-1zm3 5v3h6v-3z"/></svg>
          <span>07822254985</span>
        </li>
        <li>
          <svg viewBox="0 0 14 14"><path d="M0 3h14v8H0zm1 1v.4l6 3.8 6-3.8V4zm0 1.6V10h12V5.6L7 9.4z"/></svg>
          <span>info@renwick-tolliver.co.uk</span>
        </li>
      </ul>
    </div>

    <div class="footer-band">
      <span class="footer-url">www.renwick-tolliver.co.uk</span>
    </div>
  </section>

</body>
</html>
```